Visitenkarten-Design für Sonnen-/Fensterschutz
Zielgruppe
KLW GmbH ist eine Firma, die Sonnenschutz und Fensterschutz anbieten.
'Ihr kompetenter Partner in Sachen Sonnenschutz- , Fenster- und Türtechnik. Sie erhalten echtes Handwerk aus dem Mühlviertel zu fairen Preisen.'
Unsere Zielgruppe sind Personen mit Haus, die am Land leben.
Firmenname: KLW GmbH
Slogan: Fenster & Sonnenschutz
Aufgabenstellung
Hier befindet sich das Logodesign: https://dx.qv/t-QwLpo7RbNs
Bitte ein schlichtes Design bereitstellen mit einer Dummy-Person:
Jonas Weidlinger + Telefonnummer + Email
Die finalen Daten bitte erst am Schluss berücksichtigen (für Gewinnerdesign)
Gerne auch hintern + vorne bedruckbar bereitstellen.

```html
<!DOCTYPE html>
<html lang="de">
<head>
<meta charset="utf-8">
<title>KLW GmbH – Visitenkarte</title>
<link rel="stylesheet" href="https://fonts.googleapis.com/css2?family=Montserrat:wght@800&family=Open+Sans:wght@400&family=Poppins:wght@400&display=swap">
<style>
  :root {
    --stage: #58585a;
    --paper: #ffffff;
    --orange: #ec7a1c;
    --red: #e03b22;
    --dark-red: #a3221a;
    --text-grey: #555555;
  }
  * { margin: 0; padding: 0; box-sizing: border-box; }
  html, body { width: 1200px; height: 1200px; overflow: hidden; background: var(--stage); }
  .canvas { position: relative; width: 1200px; height: 1200px; }

  .card { position: absolute; width: 689px; overflow: hidden; }
  .card-front { left: 239px; top: 94px; height: 444px; background: var(--paper); }
  .card-back {
    left: 250px; top: 631px; height: 447px;
    background: linear-gradient(180deg, var(--orange) 0%, var(--red) 55%, var(--red) 100%);
    display: flex; align-items: center; justify-content: center;
  }

  .brand { position: absolute; right: 40px; top: 50px; text-align: right; }
  .brand-name {
    display: flex; align-items: center; justify-content: flex-end; gap: 14px;
    font-family: "Montserrat", sans-serif; font-weight: 800;
    font-size: 54px; line-height: 1; color: var(--red); letter-spacing: 1px;
  }
  .brand-square { width: 26px; height: 26px; background: var(--orange); }
  .brand-rule { height: 2px; background: var(--red); margin: 10px 0 6px; }
  .brand-slogan {
    font-family: "Montserrat", sans-serif; font-weight: 800;
    font-size: 19px; color: var(--dark-red); letter-spacing: 0.3px;
  }

  .person { position: absolute; left: 60px; top: 268px; width: 280px; text-align: center; color: var(--text-grey); font-family: "Open Sans", sans-serif; }
  .person-name { font-size: 26px; line-height: 1.2; }
  .person-role { font-size: 19px; margin-top: 6px; }

  .contact { position: absolute; left: 398px; top: 218px; font-family: "Poppins", sans-serif; color: var(--text-grey); font-size: 19px; line-height: 1.05; }
  .contact-company { font-size: 16px; margin-bottom: 12px; }
  .contact-company b { font-family: "Montserrat", sans-serif; font-weight: 800; color: #8a8a8a; font-size: 17px; }
  .contact-row { display: flex; align-items: flex-start; gap: 6px; margin-bottom: 14px; }
  .contact-row svg { flex: none; margin-top: 1px; }

  .stripes { position: absolute; left: 0; top: 378px; width: 100%; }
  .stripe-line { height: 3px; background: var(--red); margin-bottom: 10px; }
  .stripe-band { height: 12px; background: linear-gradient(90deg, var(--red), var(--orange) 50%, var(--red)); margin-bottom: 9px; }
  .stripe-band.thick { height: 14px; }
  .stripe-tag {
    position: absolute; right: 120px; top: -10px; width: 66px; height: 58px;
    background: var(--paper); display: flex; align-items: center; justify-content: center;
    font-family: "Montserrat", sans-serif; font-weight: 800; font-size: 20px; color: var(--red);
  }

  .back-name {
    display: flex; align-items: center; gap: 22px;
    font-family: "Montserrat", sans-serif; font-weight: 800; font-size: 84px; color: var(--paper); letter-spacing: 2px;
  }
  .back-circle { width: 40px; height: 40px; border-radius: 50%; background: var(--paper); }
</style>
</head>
<body>
<div class="canvas">

  <section class="card card-front" aria-label="Vorderseite">
    <div class="brand">
      <div class="brand-name"><span class="brand-square"></span>KLW GmbH</div>
      <div class="brand-rule"></div>
      <div class="brand-slogan">FENSTER &amp; SONNENSCHUTZ</div>
    </div>

    <div class="person">
      <div class="person-name">Jonas Weidlinger</div>
      <div class="person-role">Geschäftsführer</div>
    </div>

    <div class="contact">
      <div class="contact-company"><b>KLW</b> GmbH</div>
      <div class="contact-row">
        <svg width="24" height="22" viewBox="0 0 24 22"><path d="M1 1 L23 11 L1 21 L6 11 Z" fill="var(--red)"/></svg>
        <span>Am Lindenhang 7-9<br>30519 Hannover</span>
      </div>
      <div class="contact-row">
        <svg width="22" height="22" viewBox="0 0 24 24"><path d="M6.6 10.8a15 15 0 0 0 6.6 6.6l2.2-2.2a1 1 0 0 1 1-.25 11.4 11.4 0 0 0 3.6.57 1 1 0 0 1 1 1V20a1 1 0 0 1-1 1A17 17 0 0 1 3 4a1 1 0 0 1 1-1h3.5a1 1 0 0 1 1 1c0 1.25.2 2.45.57 3.57a1 1 0 0 1-.25 1z" fill="var(--red)"/></svg>
        <span>+49 151 240 6187</span>
      </div>
      <div class="contact-row">
        <svg width="22" height="22" viewBox="0 0 24 24"><rect x="2" y="5" width="20" height="14" rx="2" fill="var(--red)"/><path d="M3 7 L12 13 L21 7" stroke="#fff" stroke-width="2" fill="none"/></svg>
        <span>+49 151 240 6187</span>
      </div>
    </div>

    <div class="stripes">
      <div class="stripe-line"></div>
      <div class="stripe-band"></div>
      <div class="stripe-band thick"></div>
      <div class="stripe-tag">KLW</div>
    </div>
  </section>

  <section class="card card-back" aria-label="Rückseite">
    <div class="back-name"><span class="back-circle"></span>KLW GmbH</div>
  </section>

</div>
</body>
</html>
```